Commercial Rooftop Solar business needs a website

We need a website with fantastic appeal for a new company based in Melbourne called Tallow Ridge Energy. We design and install solar energy systems for commercial applications across Australia. Our market is to focus on small to medium businesses looking for solar solutions, but we will also provide our service for residential customers. We would like a beautiful 'front page' feel to our home page, using photographs of solar PV systems and/or natural imagery. Our logo uses the colours orange and black, which could easily be echoed in photographic imagery of sunset and sunrise, for example. The design should communicate quiet confidence and professionalism to a corporate marketplace.

NEW POINTS FOR BRIEF: This design also needs to be flexible to allow for additional future content, including a Support page with sub pages, FAQ's, and a Blog.

As part of this design project, we will require the coding for the website to be completed by the designer.

We have seen some websites, which we like the look and feel of: these are listed below.

brightvanepower.com.au:

• Beautiful images underlaying brief text selling points.
• Simple ‘front cover’ style home page with elegant drop-down menu, stylish simple font style.
• Home page invites exploration through the menu links, rather than trying to provide all the information up front.
• Company logo and name in the top left hand corner, contact details accessible at top right hand, seems consistent in most sites.

kelpworks.com.au

rumbofield.com:
• Same element as the others is the front-page style home page with beautiful images underlying text.

We have a webpage that we started uploading content to. You can use some of the content there in your designs: www.tallowridgeenergy.com.au

Technical Specifications:
PAGES:

Home

About Us

Solutions - Commercial
- Residential

Products - Solar Panels - Vorla Heron, Vorla TELD, Vorla QB
- Solar Inverters - Kestamo, BrilQuill
- Monitoring systems - Dunmere Metrics
- Batteries - RW

- Datasheets have been provided for reference but if it's too much work, you can use generic text and we will provide content later.

Contact Us

FUTURE PAGES (Please consider in structure, where links could be placed):

Support

FAQ's

Blog.

We could provide some content for the Support page soon, but the Blog and FAQ's are future pages which we don't want highlighted in the design as we don't yet have content.

Phone: 1800 7 BIRCH
Email: sales@tallowridgeenergy.com.au

Currently, I do not have images and text available. Please
use placeholders in the meantime. The final text and images will be uploaded for the winner once a winning design has been selected.

Target Market(s)

Primary focus is on small to medium sized business owners. Those owners will have a house which may be suitable for solar so we want to cater to residential deeper in the website.

Industry/Entity Type

Solar Energy

Coding

Coded - Design and coding required

Number of Pages Required

5+ page

Colors
f78f20
0255a3

Requirements
Must have
• Logo as per attachments.
Nice to have
• Logo can have alternate colours Eg. White on Orange or Black etc. provided colour correct logo is shown somewhere eg. footer or contact page.
• In the active site, I'd like to have:
• Very slowly zooming images - barely perceptible.
• Title text that rolls into place
• Subtle movements
• See https://plumtally.com.au/ for example

```html
<!DOCTYPE html>
<html lang="en">
<head>
<meta charset="utf-8">
<title>Residential | Tallow Ridge Energy</title>
<link rel="stylesheet" href="https://fonts.googleapis.com/css2?family=Michroma&family=Open+Sans:wght@400;600;700&display=swap">
<style>
:root{
  --accent:#f2421b;
  --ink:#1c1c1c;
  --body:#4a4a4a;
  --white:#ffffff;
  --footer:#161616;
  --footer-deep:#0b0b0b;
  --muted:#d8d8d8;
}
*{box-sizing:border-box;margin:0;padding:0}
html,body{width:1153px;height:1200px;overflow:hidden}
body{font-family:"Open Sans",sans-serif;background:var(--white);color:var(--body);position:relative}
.wide{font-family:"Michroma",sans-serif}

.hero{position:absolute;left:0;top:0;width:1153px;height:437px;
  background:linear-gradient(180deg,#5b7796 0%,#6f7f8d 22%,#3e4a5c 45%,#2a3550 70%,#4e5660 100%)}
.hero-shade{position:absolute;inset:0;background:rgba(10,20,40,.25)}
.brand{position:absolute;left:156px;top:42px;display:flex;align-items:center;gap:10px;color:var(--white);
  font-weight:700;font-size:20px;letter-spacing:.5px}
.brand-dot{width:22px;height:22px;border-radius:50%;background:var(--white)}
.top-contact{position:absolute;right:145px;top:20px;display:flex;align-items:center;gap:14px}
.phone{display:flex;align-items:center;gap:8px;color:var(--white);font-weight:700;font-size:16px}
.quote-btn{display:flex;align-items:center;gap:8px;background:var(--accent);color:var(--white);font-weight:700;font-size:15px;
  border:2px solid var(--white);border-radius:16px;height:30px;padding:0 12px 0 14px}

.nav{position:absolute;top:80px;left:429px;display:flex;font-size:10px;letter-spacing:1.1px;color:var(--white);white-space:nowrap}
.nav a{color:inherit;text-decoration:none;margin-right:34px;display:flex;align-items:center;gap:4px}
.nav a:last-child{margin-right:0}
.nav .active{color:var(--accent)}
.caret{width:0;height:0;border-left:4px solid transparent;border-right:4px solid transparent;border-top:4px solid currentColor}
.dropdown{position:absolute;left:502px;top:102px;width:120px;height:65px;background:var(--white);padding:8px 0}
.dropdown::before{content:"";position:absolute;right:2px;top:-6px;border-left:6px solid transparent;border-right:6px solid transparent;border-bottom:6px solid var(--white)}
.dropdown a{display:block;font-size:10px;letter-spacing:1px;padding:6px 0 8px 18px;color:var(--ink);text-decoration:none;font-variant:small-caps;white-space:nowrap}
.dropdown a+a{border-top:1px dashed #ddd;color:var(--accent);padding-left:16px}

.hero-title{position:absolute;left:0;width:1153px;top:226px;text-align:center;color:var(--white);font-weight:700;font-size:26px;line-height:34px}

.page-title{position:absolute;top:480px;left:0;width:1153px;display:flex;justify-content:center;align-items:center;gap:10px}
.page-title span.line{width:72px;height:2px;background:var(--ink)}
.page-title h1{font-family:"Michroma",sans-serif;font-weight:400;font-size:30px;color:var(--ink);font-variant:small-caps;letter-spacing:2px;white-space:nowrap}

.content{position:absolute;left:158px;top:571px;width:849px;font-size:12.2px;line-height:21px;text-align:justify;letter-spacing:.1px}
.content p{margin-bottom:9px}
.cta{position:absolute;left:157px;top:867px;width:231px;height:32px;border-radius:16px;background:var(--accent);color:var(--white);
  display:flex;align-items:center;justify-content:space-between;padding:0 7px 0 12px;font-size:8.6px;letter-spacing:1.2px;white-space:nowrap}
.cta-arrow{width:20px;height:20px;border-radius:50%;background:var(--white);display:flex;align-items:center;justify-content:center;flex:none}

.footer{position:absolute;left:0;top:940px;width:1153px;height:220px;background:var(--footer);color:var(--white)}
.col{position:absolute;top:30px}
.col h3{font-family:"Michroma",sans-serif;font-weight:400;font-size:13px;letter-spacing:1.5px;font-variant:small-caps;white-space:nowrap;
  padding-bottom:8px;border-bottom:1px dotted #777}
.divider{position:absolute;top:50px;width:2px;height:140px;background:linear-gradient(180deg,transparent,#2d2d2d,transparent)}
.links{list-style:none;margin-top:8px;font-size:11.5px}
.links li{height:30.6px;display:flex;align-items:center;gap:8px}
.links li::before{content:"›";color:#888;font-size:10px}
.field{width:184px;height:19px;background:var(--white);border-radius:2px;margin-top:5px;color:#555;font-size:9px;padding:3px 6px}
.field.msg{height:60px}
.submit{margin-top:7px;width:66px;height:22px;border-radius:11px;background:var(--accent);font-family:"Michroma",sans-serif;font-size:8px;display:flex;align-items:center;justify-content:center;letter-spacing:.5px;font-variant:small-caps}
.contact-list{list-style:none;font-size:12px;margin-top:8px}
.contact-list li{display:flex;align-items:center;gap:8px;height:33.5px;border-bottom:1px solid #2c2c2c;white-space:nowrap}
.contact-list li:last-child{border:0;align-items:flex-start;padding-top:8px;height:auto}
.contact-list strong{font-size:13px;display:block}
.foot-brand{position:absolute;left:858px;top:78px;width:150px;text-align:center;font-weight:700;font-size:17px;line-height:22px;color:#bdbdbd}
.abn{position:absolute;left:830px;top:181px;width:206px;text-align:center;font-size:11.5px}
.copyright{position:absolute;left:0;top:1160px;width:1153px;height:40px;background:var(--footer-deep);color:var(--muted);font-size:10.5px;display:flex;align-items:center;justify-content:center}
</style>
</head>
<body>

<header class="hero">
  <div class="hero-shade" role="img" aria-label="Photograph of solar panels mounted on a corrugated roof beside the sea"></div>
  <div class="brand"><span class="brand-dot"></span>Tallow Ridge Energy</div>
  <div class="top-contact">
    <div class="phone">
      <svg width="28" height="28" viewBox="0 0 28 28"><circle cx="14" cy="14" r="12.5" fill="none" stroke="#fff" stroke-width="2"/><path d="M10 8c1 0 2 2 2.3 3s-1 1.5-1 2 2 3.5 3 4 1.3-.8 2-.8 2.6 1.2 2.6 2-1.2 2-2.5 2C12 20 8 15 8 10.5 8 9 9 8 10 8z" fill="#fff"/></svg>
      1800 7 BIRCH
    </div>
    <div class="quote-btn">FREE QUOTE
      <svg width="20" height="20" viewBox="0 0 20 20" fill="none" stroke="#fff" stroke-width="1.4"><rect x="3" y="2" width="11" height="15" rx="1"/><path d="M6 7h5M6 10h5M6 13h3M12 16l5-5 1.5 1.5-5 5H12z"/></svg>
    </div>
  </div>
  <nav class="nav wide">
    <a href="#">HOME</a>
    <a href="#" class="active">SOLUTIONS <span class="caret"></span></a>
    <a href="#">PRODUCTS <span class="caret"></span></a>
    <a href="#">ABOUT US</a>
    <a href="#">CONTACT US</a>
  </nav>
  <div class="dropdown wide">
    <a href="#">Commercial</a>
    <a href="#">Residential</a>
  </div>
  <h2 class="hero-title">Tallow Ridge Energy Is A National Company That<br>Specialises In Solar Solutions For The Commercial<br>And Residential</h2>
</header>

<div class="page-title"><span class="line"></span><h1>Residential</h1><span class="line"></span></div>

<main class="content">
  <p>Lorem ipsum dolor sit amet, consectetur adipiscing elit. Donec sit amet orci sed massa aliquam elementum. Morbi ut tempor lacus. Nunc facilisis odio erat, quis porttitor massa laoreet ac. Phasellus ornare lacus quis est luctus aliquet. Suspendisse vestibulum sem sit amet pretium vehicula. Suspendisse potenti. Donec vitae hendrerit erat, vel bibendum arcu. Nam tincidunt massa quis auctor vehicula. Vestibulum rhoncus fringilla tortor, sit amet feugiat odio eleifend in. Integer ac convallis sapien, quis feugiat turpis.</p>
  <p>Duis id augue ut tortor luctus maximus et ac enim. Nunc vitae dolor elementum, pretium nisl vitae, interdum nunc. Nunc mollis fringilla mauris quis rhoncus. Quisque hendrerit neque vel arcu semper, quis sagittis nunc fringilla. Lorem ipsum dolor sit amet, consectetur adipiscing elit. Praesent pretium ante nec sollicitudin rutrum. Aenean non odio volutpat, imperdiet magna nec, commodo elit. Nulla et leo faucibus, tempus sapien in, vestibulum sem. Aliquam ultricies erat nisl, ac posuere ante suscipit non. Nam urna lorem, eleifend nec placerat at, mollis facilisis turpis. Morbi id urna rhoncus, maximus libero ac, facilisis dui.</p>
  <p>Curabitur sed diam ut ipsum fringilla porta. Nam finibus dapibus metus nec suscipit. Nam pulvinar, tortor nec malesuada hendrerit, mauris erat vulputate neque, at viverra leo mi a elit. In non feugiat sapien, nec semper metus. Donec gravida a augue ut pretium. Sed quis facilisis magna. Maecenas iaculis vitae est at vestibulum. Vestibulum in leo sapien.</p>
</main>

<a class="cta wide"><span>REQUEST A FREE QUOTE</span>
  <span class="cta-arrow"><svg width="10" height="10" viewBox="0 0 10 10"><path d="M3 1l4 4-4 4" fill="none" stroke="#111" stroke-width="2"/></svg></span>
</a>

<footer class="footer">
  <div class="col" style="left:160px;width:106px">
    <h3>Quick Links</h3>
    <ul class="links"><li>Home</li><li>Solutions</li><li>Products</li><li>About Us</li><li>Contact Us</li></ul>
  </div>
  <div class="divider" style="left:309px"></div>
  <div class="col" style="left:353px;width:184px">
    <h3>Quick Inquiry</h3>
    <div class="field" style="margin-top:12px">Name</div>
    <div class="field">Email</div>
    <div class="field msg">Message</div>
    <div class="submit">Submit</div>
  </div>
  <div class="divider" style="left:559px"></div>
  <div class="col" style="left:587px;width:193px">
    <h3>Contact Details</h3>
    <ul class="contact-list">
      <li><svg width="11" height="11" viewBox="0 0 12 12"><path d="M3 0c1 0 2 2 2 3s-1 1-1 1.5 1.5 3 2.5 3.3 1-.6 1.5-.6S11 8.5 11 9.3 10 12 8.5 12C4 12 0 8 0 3.5 0 1.5 2 0 3 0z" fill="var(--accent)"/></svg>1800 7 BIRCH</li>
      <li><svg width="12" height="9" viewBox="0 0 12 9"><rect width="12" height="9" fill="var(--accent)"/><path d="M0 0l6 5 6-5" fill="none" stroke="#161616" stroke-width="1.2"/></svg>info@tallowridgeenergy.com.au</li>
      <li><svg width="11" height="11" viewBox="0 0 12 12" fill="none" stroke="var(--accent)" stroke-width="1.2"><circle cx="6" cy="6" r="5.2"/><ellipse cx="6" cy="6" rx="2.2" ry="5.2"/><path d="M1 6h10"/></svg>www.tallowridgeenergy.com.au</li>
      <li><svg width="10" height="13" viewBox="0 0 10 13"><path d="M5 0a5 5 0 0 1 5 5c0 3-5 8-5 8S0 8 0 5a5 5 0 0 1 5-5z" fill="var(--accent)"/><circle cx="5" cy="5" r="1.8" fill="#161616"/></svg>
        <div><strong>TALLOW RIDGE ENERGY</strong>Wandin Vale, Victoria</div></li>
    </ul>
  </div>
  <div class="divider" style="left:822px"></div>
  <div class="foot-brand">Tallow Ridge<br>Energy</div>
  <div class="abn">ABN: 41 702 385 116</div>
</footer>
<div class="copyright">Copyright © 2017 Tallow Ridge Energy. All Right Reserved.</div>

</body>
</html>
```